Retail Product Label Design

We need a 4" w X 3" h label. The label will be applied to a stand up zip lock clear poly bag. 2" at the bottom of the bag will remain clear as a window to the product. The product is small packs of minerals that are placed in fruit, vegetable and flower storage. please go to www.sackpalo.com for more info. We are thinking a green color with fruits and vegetables included similar to what we use now (see attached file). We would like to consider a retro-style (bright colors almost cartoonish like the labels on TK's Alehall Beer Labels and glasses. We have exact specs for the layout when necessary. They can be found @ http://www.wrapcratemart.com/images/main/wcm-label-requirements.pdf. We would also like to freshen up our logo (see attached file). This will be one of possibly 3 labels. One label will focus on fruits and vegetables, one will focus on flowers and one will focus on valuables like electronics, cameras and silver jewelry. Colors should be limited to 5 or possibly 6.
Target Market(s)
Grocery store fruit and vegetable buyers
Industry/Entity Type
Electronics
Look and feel
Each slider illustrates characteristics of the customer's brand and the style your logo design should communicate.

```html
<!DOCTYPE html>
<html lang="en">
<head>
<meta charset="utf-8">
<title>SackPalo – Produce Label</title>
<link rel="stylesheet" href="https://fonts.googleapis.com/css2?family=Courgette&family=Exo+2:wght@600&display=swap">
<style>
  :root {
    --lime: #c9e21e;
    --lime-pale: #f4fbc8;
    --crest-inner: #8fd03e;
    --green-deep: #0b5a22;
    --green-mid: #1f8a3a;
    --green-bright: #3fae4e;
    --white: #ffffff;
    --name-yellow: #d9ea2c;
  }
  html, body {
    margin: 0;
    padding: 0;
    width: 1200px;
    height: 900px;
    overflow: hidden;
    background: var(--white);
  }
  .label {
    display: block;
    width: 1200px;
    height: 900px;
  }
  .brand-name {
    font-family: "Exo 2", sans-serif;
    font-weight: 600;
  }
  .tagline {
    font-family: "Courgette", cursive;
    fill: var(--white);
    stroke: var(--green-deep);
    stroke-width: 2.2;
    paint-order: stroke;
  }
</style>
</head>
<body>
<svg class="label" viewBox="0 0 800 600" xmlns="http://www.w3.org/2000/svg">
  <defs>
    <radialGradient id="panel-fill" cx="50%" cy="45%" r="60%">
      <stop offset="0%" stop-color="var(--green-bright)"/>
      <stop offset="55%" stop-color="var(--green-mid)"/>
      <stop offset="100%" stop-color="var(--green-deep)"/>
    </radialGradient>
    <radialGradient id="produce-fill" cx="50%" cy="50%" r="50%">
      <stop offset="0%" stop-color="#c9a46a"/>
      <stop offset="45%" stop-color="#b08450"/>
      <stop offset="80%" stop-color="#6f8a3a" stop-opacity="0.6"/>
      <stop offset="100%" stop-color="#2f8a3c" stop-opacity="0"/>
    </radialGradient>
  </defs>

  <!-- top crest: plain shape -->
  <ellipse class="crest" cx="400" cy="112" rx="165" ry="110" fill="var(--lime)"/>

  <!-- outer badge -->
  <path class="badge-frame" fill="var(--lime)"
        d="M0 330 Q30 210 95 122 Q250 95 400 92 Q550 95 705 122 Q770 210 800 330 Q770 450 705 560 Q550 600 400 600 Q250 600 95 560 Q30 450 0 330 Z"/>
  <path class="badge-inner-line" fill="none" stroke="var(--lime-pale)" stroke-width="3"
        d="M10 330 Q38 214 101 131 Q252 105 400 102 Q548 105 699 131 Q762 214 790 330 Q762 446 699 551 Q548 590 400 590 Q252 590 101 551 Q38 446 10 330 Z"/>

  <!-- crest inner: plain shape -->
  <ellipse class="crest-inner" cx="400" cy="115" rx="135" ry="95" fill="var(--crest-inner)"/>

  <!-- green panel -->
  <ellipse class="panel" cx="400" cy="340" rx="388" ry="228" fill="url(#panel-fill)"/>

  <!-- brand mark -->
  <g class="brand-mark">
    <circle cx="400" cy="82" r="26" fill="var(--white)"/>
    <text class="brand-name" x="400" y="162" text-anchor="middle" font-size="20" fill="var(--white)">SackPalo</text>
  </g>

  <!-- produce basket area -->
  <g role="img" aria-label="Photo of a wicker basket filled with fresh vegetables: corn, peppers, tomatoes, garlic and eggplant">
    <ellipse cx="405" cy="345" rx="215" ry="165" fill="url(#produce-fill)"/>
  </g>

  <!-- tagline -->
  <text class="tagline" font-size="74" textLength="670" lengthAdjust="spacing"
        transform="translate(98 455) rotate(-21)">with no special</text>
  <text class="tagline" font-size="52" textLength="600" lengthAdjust="spacing"
        transform="translate(160 490) rotate(-20.5)">bags or containers</text>

  <!-- footer name -->
  <text class="brand-name" x="400" y="530" text-anchor="middle" font-size="22" letter-spacing="2" fill="var(--name-yellow)">SackPalo</text>
</svg>
</body>
</html>
```